Wordpress Design Project for Medical clinic

I am a PODIATRY clinic: My current domain is www.corvanstepcare.com.au

I treat heel pain. ( Pain in the heel of the foot ) in Sydney, Australia

The majority of my patients are approximately 50 years of age, but some are younger and sporty. I treat runners, walkers, golfers and other sports such as boot camp.

My work is similar to that of a physiotherapist.

Target Market(s)

Industry/Entity Type

Clinic

Requirements
Must have
• My video on the home page ( autoplay )
My logo (i have a new logo which i will attach / share via dropbox)
Pictures
Sliders
information / content / contact details phone numbers
Nice to have
• Clinical feel / medical vibe

```html
<!DOCTYPE html>
<html lang="en">
<head>
<meta charset="utf-8">
<title>Corvan Step Care – Plantar Fasciitis treatment</title>
<link href="https://fonts.googleapis.com/css2?family=Questrial&display=swap" rel="stylesheet">
<style>
:root{
  --band:#a7c4e2;
  --navy:#1f4a7a;
  --blue:#5b97d3;
  --text:#4a4a4a;
  --grey:#7a7a7a;
  --white:#ffffff;
  --box-head:#2f5f93;
}
*{margin:0;padding:0;box-sizing:border-box}
html,body{width:1194px;height:1200px;overflow:hidden;background:var(--white)}
body{font-family:"Questrial",sans-serif;color:var(--text);position:relative}
a{color:inherit;text-decoration:none}

.site-header{position:absolute;left:0;top:0;width:1194px;height:161px}
.brand{position:absolute;left:100px;top:96px;display:flex;align-items:center;gap:8px}
.brand-dot{width:14px;height:14px;border-radius:50%;background:var(--blue)}
.brand-name{font-size:22px;color:#555;letter-spacing:.5px}
.header-phone{position:absolute;right:206px;top:32px;display:flex;align-items:center;gap:6px;font-size:25px;color:var(--blue)}
.header-phone .sep{color:#bbb;margin-left:6px}
.social{position:absolute;right:123px;top:31px;display:flex;gap:4px}
.social span{width:27px;height:27px;border-radius:50%;background:#4a4a4a;display:block}
.tagline{position:absolute;right:127px;top:80px;font-size:17px;color:#555;letter-spacing:.3px}
.search{position:absolute;left:836px;top:114px;width:240px;height:37px;border:1px solid #c9c9c9;display:flex;align-items:center;padding:0 14px;font-size:11px;color:#888;justify-content:space-between}

.main-nav{position:absolute;left:0;top:161px;width:1194px;height:66px;background:var(--band);display:flex;justify-content:center;align-items:center;gap:22px;font-size:12.5px;color:var(--white);letter-spacing:.3px;padding-left:8px}

.hero{position:absolute;left:0;top:227px;width:1194px;height:298px;background:radial-gradient(ellipse at center,#fafafa 0%,#efefef 70%,#e4e4e4 100%)}
.video-frame{position:absolute;left:135px;top:17px;width:461px;height:259px;background:#fff;border:1px solid #ddd;padding:6px}
.video-still{width:100%;height:100%;background:linear-gradient(135deg,#8a8f86 0%,#5f6a5e 40%,#3a3f3a 70%,#6d6a60 100%);position:relative}
.video-play{position:absolute;left:187px;top:95px}
.video-bar{position:absolute;left:4px;right:4px;bottom:6px;height:24px;background:#1d1d1d}
.video-bar .progress{position:absolute;left:0;top:-3px;height:3px;width:188px;background:#c00}
.slide-text{position:absolute;right:129px;top:100px;text-align:right;width:460px}
.slide-text h2{font-weight:400;font-size:28px;color:#333;letter-spacing:.4px}
.slide-text p{font-size:14px;line-height:24px;color:#555;margin-top:12px;letter-spacing:.3px}
.dots{position:absolute;right:129px;top:207px;display:flex;gap:3px}
.dots span{width:16px;height:16px;border-radius:50%;background:#9d9d9d}
.dots span.active{background:var(--band)}

.welcome{position:absolute;left:130px;top:550px;width:944px;text-align:center}
.welcome h1{font-weight:400;font-size:19px;color:var(--navy);letter-spacing:.4px}
.welcome p{margin-top:18px;font-size:11.8px;line-height:24px;color:var(--text);letter-spacing:.2px}

.col-title{position:absolute;top:731px;font-weight:400;font-size:19px;color:var(--navy);letter-spacing:.3px}
.panel{position:absolute;top:764px;width:301px;height:297px;background:var(--band);color:var(--white)}

.clinic{position:absolute;left:20px;display:flex;gap:16px}
.clinic svg{flex:none}
.clinic-info{font-size:12.5px;line-height:24px;letter-spacing:.2px}
.clinic-info strong{color:var(--box-head);font-weight:400;font-size:12.5px;letter-spacing:.4px}

.quote{position:absolute;left:8px;top:44px;right:6px}
.quote p{padding-left:25px;font-size:16.5px;line-height:24px;margin-top:2px;letter-spacing:.2px}
.quote cite{display:block;font-style:normal;font-size:18px;padding-left:25px;margin-top:22px;letter-spacing:.3px}

.call{position:absolute;left:21px;top:32px;right:16px}
.call h3{font-weight:400;font-size:18px;color:var(--box-head);letter-spacing:1px}
.call .numbers{margin-top:26px;font-size:14px;line-height:24px;letter-spacing:.2px}
.btn{display:block;margin:14px 0 0 4px;width:251px;height:46px;background:linear-gradient(#fff,#e4e4e4);border-radius:3px;box-shadow:0 2px 4px rgba(0,0,0,.3);color:#222;font-size:19px;text-align:center;line-height:46px;letter-spacing:.5px}
.call .note{margin-top:16px;font-size:12.5px;line-height:24px;letter-spacing:.2px}
.call .note a{color:var(--box-head)}

.site-footer{position:absolute;left:0;top:1105px;width:1194px;height:95px;background:var(--band);color:var(--white);text-align:center}
.footer-nav{display:flex;justify-content:center;gap:21px;font-size:12.5px;margin-top:17px;letter-spacing:.2px}
.copyright{margin-top:24px;font-size:12.5px;letter-spacing:.2px}
</style>
</head>
<body>

<header class="site-header">
  <div class="brand"><span class="brand-dot"></span><span class="brand-name">Corvan Step Care</span></div>
  <div class="header-phone">
    <svg width="22" height="28" viewBox="0 0 22 28"><path d="M5 1c2 0 3 1 4 4l1 3c0 2-2 2-3 3 0 3 2 7 5 9 1-1 2-2 3-2l3 2c2 2 2 3 1 4l-2 2c-4 2-9-3-12-9S0 4 3 2z" fill="#555"/></svg>
    <span>02 9000 4417</span><span class="sep">|</span>
  </div>
  <div class="social"><span></span><span></span></div>
  <div class="tagline">Plantar Fasciitis treatment</div>
  <div class="search"><span>Type search</span>
    <svg width="16" height="16" viewBox="0 0 16 16"><circle cx="6.5" cy="6.5" r="4.5" fill="none" stroke="#999" stroke-width="1.4"/><line x1="10" y1="10" x2="14" y2="14" stroke="#999" stroke-width="2"/></svg>
  </div>
</header>

<nav class="main-nav">
  <a href="#">Home</a><a href="#">About Ewan</a><a href="#">What is Plantar Fasciitis?</a><a href="#">What causes Plantar Fasciitis?</a><a href="#">Unsuccessful Treatments</a><a href="#">Plantar Fasciitis Treatment</a><a href="#">Contact Us</a>
</nav>

<section class="hero">
  <div class="video-frame">
    <div class="video-still" role="img" aria-label="Introductory video of the podiatrist speaking on a coastal walkway">
      <svg class="video-play" width="74" height="50" viewBox="0 0 74 50"><rect x="1" y="1" width="72" height="48" rx="9" fill="#1a1a1a" stroke="#888"/><path d="M28 13 L50 25 L28 37Z" fill="#fff"/></svg>
      <div class="video-bar"><div class="progress"></div></div>
    </div>
  </div>
  <div class="slide-text">
    <h2>Lorem Ipsum is simply dummy</h2>
    <p>Printing and typesetting industry. Lorem Ipsum has been the industry's standard dummy text</p>
  </div>
  <div class="dots"><span class="active"></span><span></span><span></span><span></span></div>
</section>

<section class="welcome">
  <h1>Welcome to Corvan Step Care</h1>
  <p>Lorem Ipsum is simply dummy text of the printing and typesetting industry. Lorem Ipsum has been the industry's standard dummy text ever since the 1500s, when an unknown printer took a galley of type and scrambled it to make a type specimen book. It has survived not only five centuries, but also the leap into electronic typesetting, remaining essentially unchanged. Lorem Ipsum is simply dummy text of the printing and typesetting industry. Lorem Ipsum has been the industry's standard dummy text ever since the 1500s, when an unknown printer took a galley of type and scrambled it to make a type specimen book. It has survived not only five centuries, but also the leap into electronic typesetting, remaining essentially unchanged.</p>
</section>

<h2 class="col-title" style="left:131px">Clinic Locations</h2>
<h2 class="col-title" style="left:449px">Patient Education</h2>
<h2 class="col-title" style="left:769px">Make An Appointment</h2>

<div class="panel" style="left:130px">
  <div class="clinic" style="top:44px">
    <svg width="62" height="56" viewBox="0 0 62 56"><path d="M3 14 L21 10 L41 14 L59 10 L59 50 L41 54 L21 50 L3 54Z" fill="#8cc46a" stroke="#fff" stroke-width="2"/><path d="M41 14 L59 10 L59 50 L41 54Z" fill="#5aa0d8"/><path d="M30 2c-6 0-9 5-7 10l7 14 7-14c2-5-1-10-7-10z" fill="#e8612c"/><circle cx="30" cy="9" r="3" fill="#fff"/></svg>
    <div class="clinic-info"><strong>SYDNEY CITY CLINIC</strong><br>14-18 Harlow Street<br>Sydney 2000<br>Tel: 02 9000 4417</div>
  </div>
  <div class="clinic" style="top:164px">
    <svg width="62" height="56" viewBox="0 0 62 56"><path d="M3 14 L21 10 L41 14 L59 10 L59 50 L41 54 L21 50 L3 54Z" fill="#8cc46a" stroke="#fff" stroke-width="2"/><path d="M41 14 L59 10 L59 50 L41 54Z" fill="#5aa0d8"/><path d="M30 2c-6 0-9 5-7 10l7 14 7-14c2-5-1-10-7-10z" fill="#e8612c"/><circle cx="30" cy="9" r="3" fill="#fff"/></svg>
    <div class="clinic-info"><strong>RYDE CLINIC</strong><br>22-24 Wendell Road<br>Ryde<br>NSW 2112<br>Tel: 02 9000 5528</div>
  </div>
</div>

<div class="panel" style="left:450px">
  <div class="quote">
    <svg width="30" height="22" viewBox="0 0 30 22"><circle cx="7" cy="14" r="6" fill="#3a3a3a"/><path d="M1 14 Q2 3 11 1 L12 3 Q6 6 6 12Z" fill="#3a3a3a"/><circle cx="22" cy="14" r="6" fill="#3a3a3a"/><path d="M16 14 Q17 3 26 1 L27 3 Q21 6 21 12Z" fill="#3a3a3a"/></svg>
    <p>Its not just about me implementing treatments and therapies, its also crucial that the patients stop doing the things that aggravate the heel <svg width="30" height="22" viewBox="0 0 30 22" style="vertical-align:-8px"><g transform="rotate(180 15 11)"><circle cx="7" cy="14" r="6" fill="#3a3a3a"/><path d="M1 14 Q2 3 11 1 L12 3 Q6 6 6 12Z" fill="#3a3a3a"/><circle cx="22" cy="14" r="6" fill="#3a3a3a"/><path d="M16 14 Q17 3 26 1 L27 3 Q21 6 21 12Z" fill="#3a3a3a"/></g></svg></p>
    <cite>Ewan Marsh</cite>
  </div>
</div>

<div class="panel" style="left:770px">
  <div class="call">
    <h3>CALL US NOW</h3>
    <div class="numbers">Sydney City Clinic - 9000 4417<br>Ryde Clinic - 9000 5528</div>
    <a class="btn" href="#">Make an appointment</a>
    <p class="note">Alternatively please fill in the contact form and one of our experienced staff will get back to you as soon as possible. <a href="#">Read More</a></p>
  </div>
</div>

<footer class="site-footer">
  <nav class="footer-nav">
    <a href="#">Home</a><a href="#">About Ewan</a><a href="#">What is Plantar Fasciitis?</a><a href="#">What causes Plantar Fasciitis?</a><a href="#">Unsuccessful Treatments</a><a href="#">Plantar Fasciitis Treatment</a><a href="#">Contact Us</a>
  </nav>
  <p class="copyright">Copyright ©2013 Company Name &nbsp; - All rights reserved</p>
</footer>

</body>
</html>
```